Folder Design: Mobile Laboratory Service

Need a folder designed for a Mobile Laboratory Service. Folder needs to be very professional and will be used to hold brochure, contract and business card of business. Logos of the company are attached.

Industry/Entity Type

Healthcare

```html
<!DOCTYPE html>
<html lang="en">
<head>
<meta charset="utf-8">
<title>Vantage Mobile Labs – Presentation Folder</title>
<link rel="stylesheet" href="https://fonts.googleapis.com/css2?family=Lexend:wght@400;500;600;700&family=Poppins:wght@300;400;500&display=swap">
<style>
:root{
  --stage-dark:#2b2b2b;
  --stage-gray:#d6d6d6;
  --navy:#0f3b78;
  --blue:#1b5597;
  --accent:#1f63a8;
  --ring:#6c9bd3;
  --white:#ffffff;
  --muted:#7d8fb0;
  --ink:#1d3357;
  --fold:#9a9a9a;
}
*{margin:0;padding:0;box-sizing:border-box}
html,body{width:1200px;height:3563px;overflow:hidden}
body{position:relative;background:var(--stage-gray);font-family:"Poppins",sans-serif;color:var(--white)}
.abs{position:absolute}

.stage-top{position:absolute;left:0;top:0;width:1200px;height:733px;background:var(--stage-dark)}
.stage-row{position:absolute;left:0;top:733px;width:1200px;height:657px;background:var(--stage-dark);border-top:1px solid #3a3a3a}
.stage-sheet{position:absolute;left:40px;width:1108px;background:var(--stage-gray)}
.page-light{position:absolute;left:0;top:1390px;width:1200px;height:2173px;background:#fff}

.scaler{position:absolute;transform-origin:0 0}

.cell-field{position:absolute;inset:0;
  background:
    radial-gradient(ellipse at 20% 30%,rgba(120,170,225,.35),transparent 45%),
    radial-gradient(ellipse at 80% 60%,rgba(10,40,95,.45),transparent 50%),
    radial-gradient(ellipse at 60% 15%,rgba(90,140,205,.3),transparent 40%),
    linear-gradient(160deg,#215f9f 0%,#174c8b 50%,#0f3b78 100%)}

/* front cover */
.cover{position:absolute;left:0;top:0;width:487px;height:674px;overflow:hidden;text-align:center;font-family:"Lexend",sans-serif}
.cover .wave{position:absolute;left:0;top:0}
.cover-line{position:absolute;left:0;width:100%;font-weight:600;letter-spacing:.01em}
.cover-brand{top:60px;font-size:15px}
.cover-kicker{top:114px;font-size:19px;font-weight:500}
.cover-title{top:150px;font-size:50px;font-weight:700;line-height:1.1;text-shadow:0 2px 6px rgba(0,0,0,.35);color:#e9f1fb}
.cover-years{top:476px;font-size:34px;font-weight:600;line-height:1.1}
.cover-tag{top:636px;font-size:11px;font-weight:500;color:var(--ink)}

.mark{position:absolute;border-radius:50%;display:flex;align-items:center;justify-content:center;font-family:"Lexend",sans-serif;font-weight:600}
.mark-light{border:3px solid var(--ring);color:#dce8f7}
.mark-dark{border:3px solid var(--accent);color:var(--accent)}

/* spreads */
.spread{position:absolute;left:0;top:0;width:974px;height:674px;overflow:hidden;background:#fff}
.panel{position:absolute;top:0;width:487px;height:674px;overflow:hidden}
.fold-v{position:absolute;left:487px;top:0;width:0;height:674px;border-left:1px dashed var(--fold)}

.photo{position:absolute;border-radius:50%;border:4px solid var(--ring);box-shadow:0 0 0 2px rgba(255,255,255,.25)}
.photo-lab{background:radial-gradient(circle at 40% 35%,#9cc3ea,#3d72b0 50%,#143f78)}
.photo-dish{background:radial-gradient(circle at 50% 55%,#e7a35f,#b76a3c 45%,#2a4c7a 80%)}
.photo-sample{background:radial-gradient(circle at 50% 55%,#e6a0b8,#7aa6d8 45%,#1c4c8d 85%)}

.back-eyebrow{left:39px;top:380px;font-family:"Lexend",sans-serif;font-weight:600;font-size:18px;color:var(--accent)}
.back-head{left:39px;top:408px;font-family:"Lexend",sans-serif;font-weight:700;font-size:33px;line-height:1.15;color:var(--accent)}
.divider{left:205px;top:524px;width:1px;height:134px;background:#8c99ad}
.contact{position:absolute;left:225px;display:flex;align-items:flex-start;gap:9px;font-size:10px;color:var(--ink);line-height:1.45}
.contact svg{flex:none}

.about-title{left:0;width:487px;top:302px;text-align:center;font-family:"Lexend",sans-serif;font-weight:600;font-size:18px}
.about-copy{left:51px;top:332px;width:388px;font-size:10.5px;line-height:1.45;text-align:justify}
.checks{position:absolute;left:51px;top:566px;width:400px;display:grid;grid-template-columns:144px 115px 140px;row-gap:12px}
.check{display:flex;align-items:center;gap:7px;font-size:11px;color:var(--muted)}

.pocket{position:absolute}
.pocket-folded{position:absolute;left:520px;top:466px;width:454px;height:208px;background:linear-gradient(180deg,#e9eaec,#f7f7f8);box-shadow:0 -3px 8px rgba(0,0,0,.15)}
</style>
</head>
<body>

<section class="stage-top">
  <div class="scaler" style="left:450px;top:160px;transform:scale(.616)">
    <div class="cover">
      <div class="cell-field" role="img" aria-label="Blue microscopic cell texture"></div>
      <svg class="wave" width="487" height="674"><path d="M0,600 C150,615 330,600 487,500 L487,674 L0,674 Z" fill="#fff"/></svg>
      <p class="cover-line cover-brand">VANTAGE MOBILE LABS</p>
      <p class="cover-line cover-kicker">CUTTING-EDGE PATHOLOGY LAB</p>
      <h1 class="cover-line cover-title">DIAGNOSING<br>THE FUTURE</h1>
      <div class="mark mark-light" style="left:188px;top:300px;width:112px;height:112px;font-size:30px">VML</div>
      <p class="cover-line cover-years">50 YEARS<br>OF EXPERIENCE</p>
      <p class="cover-line cover-tag">LABORATORY AND PHLEBOTOMY SERVICES</p>
    </div>
  </div>
</section>

<section class="stage-row">
  <div class="scaler" style="left:62px;top:76px;transform:scale(.692)">
    <div class="spread">
      <div class="cell-field" role="img" aria-label="Blue microscopic cell texture"></div>
      <svg class="abs" style="left:0;top:0" width="974" height="674"><path d="M0,458 C90,540 200,560 300,520 C400,500 440,450 487,440 C650,380 820,300 974,280 L974,674 L0,674 Z" fill="#fff"/></svg>
      <div class="photo photo-lab" style="left:119px;top:30px;width:250px;height:250px" role="img" aria-label="Scientist at a microscope"></div>
      <h2 class="abs about-title">Vantage Mobile Labs</h2>
      <p class="abs about-copy">Vantage Mobile Labs has a wide range of laboratory testing that covers the following disease states: Anemia, Bone/Skeleton, Cardiac, Diabetes, Drugs of Abuse, General Chemistry, Hepatic, Immunosuppressant Drugs, Infectious Disease, Inflammatory, Lipids, Microbiology, Mycology, Nutritional Assessment, Oncology, Pancreatic, Parasitology, Prenatal, Renal, Reproductive Endocrinology, Respiratory, Sepsis, Spinal, Therapeutic Drug Monitoring, Metabolic, Toxicology, Urinalysis and Virology.</p>
      <div class="checks">
        <span class="check"><svg width="13" height="13" viewBox="0 0 14 14"><circle cx="7" cy="7" r="6" fill="none" stroke="#5b8fd0" stroke-width="1.2"/><path d="M4 7.2 6.2 9.3 10.5 4.5" fill="none" stroke="#5b8fd0" stroke-width="1.5"/></svg>Clinical Chemistry</span>
        <span class="check"><svg width="13" height="13" viewBox="0 0 14 14"><circle cx="7" cy="7" r="6" fill="none" stroke="#5b8fd0" stroke-width="1.2"/><path d="M4 7.2 6.2 9.3 10.5 4.5" fill="none" stroke="#5b8fd0" stroke-width="1.5"/></svg>Parasitology</span>
        <span class="check"><svg width="13" height="13" viewBox="0 0 14 14"><circle cx="7" cy="7" r="6" fill="none" stroke="#5b8fd0" stroke-width="1.2"/><path d="M4 7.2 6.2 9.3 10.5 4.5" fill="none" stroke="#5b8fd0" stroke-width="1.5"/></svg>Immunohematology</span>
        <span class="check"><svg width="13" height="13" viewBox="0 0 14 14"><circle cx="7" cy="7" r="6" fill="none" stroke="#5b8fd0" stroke-width="1.2"/><path d="M4 7.2 6.2 9.3 10.5 4.5" fill="none" stroke="#5b8fd0" stroke-width="1.5"/></svg>Mycology</span>
        <span class="check"><svg width="13" height="13" viewBox="0 0 14 14"><circle cx="7" cy="7" r="6" fill="none" stroke="#5b8fd0" stroke-width="1.2"/><path d="M4 7.2 6.2 9.3 10.5 4.5" fill="none" stroke="#5b8fd0" stroke-width="1.5"/></svg>Urinalysis</span>
        <span class="check"><svg width="13" height="13" viewBox="0 0 14 14"><circle cx="7" cy="7" r="6" fill="none" stroke="#5b8fd0" stroke-width="1.2"/><path d="M4 7.2 6.2 9.3 10.5 4.5" fill="none" stroke="#5b8fd0" stroke-width="1.5"/></svg>Tumor Markers</span>
        <span class="check"><svg width="13" height="13" viewBox="0 0 14 14"><circle cx="7" cy="7" r="6" fill="none" stroke="#5b8fd0" stroke-width="1.2"/><path d="M4 7.2 6.2 9.3 10.5 4.5" fill="none" stroke="#5b8fd0" stroke-width="1.5"/></svg>Microbiology</span>
        <span class="check"><svg width="13" height="13" viewBox="0 0 14 14"><circle cx="7" cy="7" r="6" fill="none" stroke="#5b8fd0" stroke-width="1.2"/><path d="M4 7.2 6.2 9.3 10.5 4.5" fill="none" stroke="#5b8fd0" stroke-width="1.5"/></svg>Hematology</span>
        <span class="check"><svg width="13" height="13" viewBox="0 0 14 14"><circle cx="7" cy="7" r="6" fill="none" stroke="#5b8fd0" stroke-width="1.2"/><path d="M4 7.2 6.2 9.3 10.5 4.5" fill="none" stroke="#5b8fd0" stroke-width="1.5"/></svg>Virology</span>
      </div>
      <div class="mark mark-light" style="left:680px;top:64px;width:126px;height:126px;font-size:32px">VML</div>
      <div class="pocket-folded">
        <svg class="abs" style="left:0;top:0" width="454" height="208"><rect x="113" y="48" width="212" height="120" rx="8" fill="none" stroke="#7f9bc8" stroke-width="1.5"/><path d="M103 58 128 38M310 178 335 158" stroke="#7f9bc8" stroke-width="1.2"/></svg>
      </div>
    </div>
  </div>
  <div class="scaler" style="left:815px;top:76px;transform:scale(.688)">
    <div class="cover">
      <div class="cell-field" role="img" aria-label="Blue microscopic cell texture"></div>
      <svg class="wave" width="487" height="674"><path d="M0,600 C150,615 330,600 487,500 L487,674 L0,674 Z" fill="#fff"/></svg>
      <p class="cover-line cover-brand">VANTAGE MOBILE LABS</p>
      <p class="cover-line cover-kicker">CUTTING-EDGE PATHOLOGY LAB</p>
      <h2 class="cover-line cover-title">DIAGNOSING<br>THE FUTURE</h2>
      <div class="mark mark-light" style="left:188px;top:300px;width:112px;height:112px;font-size:30px">VML</div>
      <p class="cover-line cover-years">50 YEARS<br>OF EXPERIENCE</p>
      <p class="cover-line cover-tag">LABORATORY AND PHLEBOTOMY SERVICES</p>
    </div>
  </div>
</section>

<div class="page-light"></div>

<section class="stage-sheet" style="top:1428px;height:996px">
  <div class="abs" style="left:83px;top:51px">
    <div class="spread">
      <div class="panel" style="left:0">
        <div class="cell-field" role="img" aria-label="Blue microscopic cell texture"></div>
        <svg class="abs" style="left:0;top:0" width="487" height="674"><path d="M0,360 C90,300 210,310 300,400 C400,470 480,560 487,674 L0,674 Z" fill="#fff"/></svg>
        <div class="photo photo-lab" style="left:35px;top:39px;width:248px;height:248px" role="img" aria-label="Scientist examining samples under a microscope"></div>
        <div class="photo photo-dish" style="left:313px;top:28px;width:124px;height:124px" role="img" aria-label="Culture dish close-up"></div>
        <div class="photo photo-sample" style="left:276px;top:186px;width:176px;height:176px" role="img" aria-label="Gloved hand holding a sample dish"></div>
        <p class="abs back-eyebrow">LABORATORY RESULTS</p>
        <h2 class="abs back-head">THAT YOU CAN<br>TRUST</h2>
        <div class="mark mark-dark" style="left:40px;top:532px;width:110px;height:110px;font-size:30px">VML</div>
        <div class="abs divider"></div>
        <div class="contact" style="top:528px"><svg width="16" height="16" viewBox="0 0 16 16"><circle cx="8" cy="8" r="7.3" fill="none" stroke="#1f63a8" stroke-width="1.2"/><path d="M5.5 4.5c.6-.5 1.2-.3 1.5.3l.5 1c.2.5 0 .9-.4 1.2.4 1 1 1.6 2 2 .3-.4.7-.6 1.2-.4l1 .5c.6.3.8.9.3 1.5-.8.9-2.3.9-4-.4-1.7-1.3-2.9-3.6-2.1-5.7z" fill="#1f63a8"/></svg><span>(555) 014-2230</span></div>
        <div class="contact" style="top:559px"><svg width="16" height="16" viewBox="0 0 16 16"><circle cx="8" cy="8" r="7.3" fill="none" stroke="#1f63a8" stroke-width="1.2"/><rect x="4.3" y="5.3" width="7.4" height="5.4" fill="none" stroke="#1f63a8" stroke-width="1.1"/><path d="M4.3 5.5 8 8.4l3.7-2.9" fill="none" stroke="#1f63a8" stroke-width="1.1"/></svg><span>hello@vmlabs.com</span></div>
        <div class="contact" style="top:590px"><svg width="16" height="16" viewBox="0 0 16 16"><circle cx="8" cy="8" r="7.3" fill="none" stroke="#1f63a8" stroke-width="1.2"/><circle cx="8" cy="8" r="3.8" fill="none" stroke="#1f63a8" stroke-width="1"/><path d="M4.2 8h7.6M8 4.2c-1.4 1.6-1.4 6 0 7.6M8 4.2c1.4 1.6 1.4 6 0 7.6" fill="none" stroke="#1f63a8" stroke-width=".9"/></svg><span>www.vmlabs.com</span></div>
        <div class="contact" style="top:621px"><svg width="16" height="16" viewBox="0 0 16 16"><circle cx="8" cy="8" r="7.3" fill="none" stroke="#1f63a8" stroke-width="1.2"/><path d="M8 12.2s-3-3.2-3-5.3a3 3 0 0 1 6 0c0 2.1-3 5.3-3 5.3z" fill="#1f63a8"/><circle cx="8" cy="6.9" r="1.1" fill="#fff"/></svg><span>418 Cedar Ridge Drive<br>Suite 210, Riverton, Nevada 89000</span></div>
      </div>
      <div class="cover" style="left:487px">
        <div class="cell-field" role="img" aria-label="Blue microscopic cell texture"></div>
        <svg class="wave" width="487" height="674"><path d="M0,600 C150,615 330,600 487,500 L487,674 L0,674 Z" fill="#fff"/></svg>
        <p class="cover-line cover-brand">VANTAGE MOBILE LABS</p>
        <p class="cover-line cover-kicker">CUTTING-EDGE PATHOLOGY LAB</p>
        <h2 class="cover-line cover-title">DIAGNOSING<br>THE FUTURE</h2>
        <div class="mark mark-light" style="left:188px;top:300px;width:112px;height:112px;font-size:30px">VML</div>
        <p class="cover-line cover-years">50 YEARS<br>OF EXPERIENCE</p>
        <p class="cover-line cover-tag">LABORATORY AND PHLEBOTOMY SERVICES</p>
      </div>
      <div class="fold-v"></div>
    </div>
  </div>
  <svg class="pocket" style="left:50px;top:725px" width="520" height="222">
    <path d="M33,0 L514,0 L484,221 L33,221 L0,207 L0,14 Z" fill="#fff" stroke="#b5b5b5"/>
    <line x1="33" y1="0" x2="33" y2="221" stroke="#9a9a9a" stroke-dasharray="5 4"/>
    <line x1="33" y1="0.5" x2="520" y2="0.5" stroke="#9a9a9a" stroke-dasharray="5 4"/>
    <rect x="169" y="53" width="210" height="120" rx="8" fill="none" stroke="#5a77b8" stroke-width="1.5"/>
    <path d="M159 68 188 40M360 186 389 158" stroke="#5a77b8" stroke-width="1.2"/>
  </svg>
</section>

<section class="stage-sheet" style="top:2497px;height:995px">
  <div class="abs" style="left:51px;top:50px">
    <div class="spread">
      <div class="cell-field" role="img" aria-label="Blue microscopic cell texture"></div>
      <svg class="abs" style="left:0;top:0" width="974" height="674"><path d="M0,458 C90,540 200,560 300,520 C400,500 440,450 487,440 C650,380 820,300 974,280 L974,674 L0,674 Z" fill="#fff"/></svg>
      <div class="photo photo-lab" style="left:119px;top:30px;width:250px;height:250px" role="img" aria-label="Scientist at a microscope"></div>
      <h2 class="abs about-title">Vantage Mobile Labs</h2>
      <p class="abs about-copy">Vantage Mobile Labs has a wide range of laboratory testing that covers the following disease states: Anemia, Bone/Skeleton, Cardiac, Diabetes, Drugs of Abuse, General Chemistry, Hepatic, Immunosuppressant Drugs, Infectious Disease, Inflammatory, Lipids, Microbiology, Mycology, Nutritional Assessment, Oncology, Pancreatic, Parasitology, Prenatal, Renal, Reproductive Endocrinology, Respiratory, Sepsis, Spinal, Therapeutic Drug Monitoring, Metabolic, Toxicology, Urinalysis and Virology.</p>
      <div class="checks">
        <span class="check"><svg width="13" height="13" viewBox="0 0 14 14"><circle cx="7" cy="7" r="6" fill="none" stroke="#5b8fd0" stroke-width="1.2"/><path d="M4 7.2 6.2 9.3 10.5 4.5" fill="none" stroke="#5b8fd0" stroke-width="1.5"/></svg>Clinical Chemistry</span>
        <span class="check"><svg width="13" height="13" viewBox="0 0 14 14"><circle cx="7" cy="7" r="6" fill="none" stroke="#5b8fd0" stroke-width="1.2"/><path d="M4 7.2 6.2 9.3 10.5 4.5" fill="none" stroke="#5b8fd0" stroke-width="1.5"/></svg>Parasitology</span>
        <span class="check"><svg width="13" height="13" viewBox="0 0 14 14"><circle cx="7" cy="7" r="6" fill="none" stroke="#5b8fd0" stroke-width="1.2"/><path d="M4 7.2 6.2 9.3 10.5 4.5" fill="none" stroke="#5b8fd0" stroke-width="1.5"/></svg>Immunohematology</span>
        <span class="check"><svg width="13" height="13" viewBox="0 0 14 14"><circle cx="7" cy="7" r="6" fill="none" stroke="#5b8fd0" stroke-width="1.2"/><path d="M4 7.2 6.2 9.3 10.5 4.5" fill="none" stroke="#5b8fd0" stroke-width="1.5"/></svg>Mycology</span>
        <span class="check"><svg width="13" height="13" viewBox="0 0 14 14"><circle cx="7" cy="7" r="6" fill="none" stroke="#5b8fd0" stroke-width="1.2"/><path d="M4 7.2 6.2 9.3 10.5 4.5" fill="none" stroke="#5b8fd0" stroke-width="1.5"/></svg>Urinalysis</span>
        <span class="check"><svg width="13" height="13" viewBox="0 0 14 14"><circle cx="7" cy="7" r="6" fill="none" stroke="#5b8fd0" stroke-width="1.2"/><path d="M4 7.2 6.2 9.3 10.5 4.5" fill="none" stroke="#5b8fd0" stroke-width="1.5"/></svg>Tumor Markers</span>
        <span class="check"><svg width="13" height="13" viewBox="0 0 14 14"><circle cx="7" cy="7" r="6" fill="none" stroke="#5b8fd0" stroke-width="1.2"/><path d="M4 7.2 6.2 9.3 10.5 4.5" fill="none" stroke="#5b8fd0" stroke-width="1.5"/></svg>Microbiology</span>
        <span class="check"><svg width="13" height="13" viewBox="0 0 14 14"><circle cx="7" cy="7" r="6" fill="none" stroke="#5b8fd0" stroke-width="1.2"/><path d="M4 7.2 6.2 9.3 10.5 4.5" fill="none" stroke="#5b8fd0" stroke-width="1.5"/></svg>Hematology</span>
        <span class="check"><svg width="13" height="13" viewBox="0 0 14 14"><circle cx="7" cy="7" r="6" fill="none" stroke="#5b8fd0" stroke-width="1.2"/><path d="M4 7.2 6.2 9.3 10.5 4.5" fill="none" stroke="#5b8fd0" stroke-width="1.5"/></svg>Virology</span>
      </div>
      <div class="mark mark-light" style="left:680px;top:64px;width:126px;height:126px;font-size:32px">VML</div>
      <div class="fold-v"></div>
    </div>
  </div>
  <svg class="pocket" style="left:537px;top:725px" width="520" height="222">
    <path d="M5,0 L486,0 L520,14 L520,207 L486,221 L40,221 Z" fill="#fff" stroke="#b5b5b5"/>
    <line x1="486" y1="0" x2="486" y2="221" stroke="#9a9a9a" stroke-dasharray="5 4"/>
    <rect x="141" y="51" width="212" height="122" rx="8" fill="none" stroke="#5a77b8" stroke-width="1.5"/>
    <path d="M333 40 362 66M133 150 162 180" stroke="#5a77b8" stroke-width="1.2"/>
  </svg>
</section>

</body>
</html>
```